Website Design for Chef Wen Chinese Restaurant

Chef Wen is a new Chinese Restaurant. It offers exceptional dining experience with authentic and dynamic dishes created with quality ingredients.

A vivid website theme is required to promote this new restaurant online. Logo, menu, wine list and a few other files are attached for help with designing.

A very rough demo website has been setup and can be accessed via http://www.chefwen.com.au. It is for telling designers what content is shown up on each page (except for homepage). By reading the about us page, designers can get some more info of Chef Wen. However, the layout, theme color, font, etc are not set in stone. Visitors should be able to feel Chef Wen restaurant's authentic Chinese cuisine and high hygiene standard. Home page of the website could be The "Our website is coming soon" description is shown on demo site but do not required to be presented on new design.

Some main pages design should be included: Home (landing page), About us, Menu (Dishes), Winelist, Gallery, Contact us. No HTML and coding required. The output should be well layered psd or png files with acceptable resolution for web use.

A few other website can be referred to are:

http://larkspurasian.com.au/
http://www.river-lamp.com/
http://tamworthy.com.au/
http://harbelrestaurant.com.au/
http://www.quillerestaurant.com.au/
http://www.thekiln.com.au/

Industry/Entity Type

Restaurant

Requirements
Nice to have
• I expect designs of at least these webpages: homepage, menu page and contact us page. If you can provide "about us" page as well, it will probably help you win the competition. well layered psd or png file is my preference.
Should not have
• You don't have to make html/cs/js or any coding. All I need is just art design

```html
<!DOCTYPE html>
<html lang="en">
<head>
<meta charset="utf-8">
<title>Chef Wen Chinese Restaurant</title>
<link href="https://fonts.googleapis.com/css2?family=Arimo:wght@400;700&family=Almendra:ital,wght@1,700&display=swap" rel="stylesheet">
<style>
:root{
  --red:#e8252a;
  --red-deep:#c8161c;
  --cream:#fffbd0;
  --nav-grey:#e3e3e3;
  --ink:#222;
  --body:#3a3a3a;
  --slate:#3c3c3c;
  --wood:#7a3a12;
  --hours-text:#fff7a8;
  --footer:#1c1c1c;
  --white:#fff;
}
*{margin:0;padding:0;box-sizing:border-box}
html,body{width:922px;height:1200px;overflow:hidden}
body{position:relative;background:var(--white);font-family:"Arimo",Arial,sans-serif;color:var(--body)}
.abs{position:absolute}

/* top bar */
.topbar{left:0;top:0;width:922px;height:40px;background:var(--red);border-bottom:2px solid #b51218}
.reservation{left:68px;top:11px;color:var(--white);font-weight:700;font-size:13px;display:flex;align-items:center;gap:6px;z-index:2}
.social{right:87px;top:3px;display:flex;gap:8px;z-index:2}
.social span{width:32px;height:32px;border-radius:50%;background:var(--white);display:flex;align-items:center;justify-content:center}

/* header */
.header{left:0;top:40px;width:922px;height:98px;background:var(--cream);border-bottom:2px solid #555}
.ornament{top:50px;width:180px;height:78px;background:linear-gradient(90deg,#f6a25a,#e0501e,#f6a25a);border-radius:39px;opacity:.75}
.ornament.left{left:138px}
.ornament.right{left:572px}
.logo-arch{left:352px;top:6px;width:186px;height:132px;background:var(--cream);border-radius:93px 93px 0 0;border-top:2px solid #e9b99c;display:flex;flex-direction:column;align-items:center;justify-content:center;gap:6px;padding-top:18px}
.logo-arch .mark{width:16px;height:16px;background:var(--red)}
.logo-arch .name{font-weight:700;font-size:12px;color:var(--ink);text-align:center;line-height:1.3}

/* nav */
.nav{left:0;top:140px;width:922px;height:39px;background:var(--nav-grey);font-size:16px}
.nav a{position:absolute;top:9px;text-decoration:none;color:var(--red)}
.nav a.active{color:#111}

/* hero */
.hero{left:0;top:179px;width:922px;height:241px;background:linear-gradient(90deg,#7a2a1c 0%,#b83a2c 25%,#d9c8c0 45%,#8a6c58 65%,#3b2a1c 85%,#5a3a22 100%)}
.dots{left:432px;top:428px;display:flex;gap:8px}
.dots span{width:8px;height:8px;border-radius:50%;background:#333}
.dots span.on{background:var(--red)}

/* welcome */
.welcome-title{left:69px;top:458px;width:516px;text-align:center;font-size:22px;color:var(--ink)}
.divider{left:70px;top:484px;width:486px;height:36px}
.welcome-text{left:69px;top:521px;width:500px;font-size:11px;line-height:17.6px;color:var(--body)}
.welcome-text p+p{margin-top:17.6px}
.read-more{left:478px;top:672px;width:96px;height:32px;background:var(--red);color:var(--white);font-weight:700;font-size:12px;display:flex;align-items:center;justify-content:center}

/* hours */
.hours{left:598px;top:461px;width:256px;height:240px;background:var(--wood);padding:7px}
.hours-inner{width:100%;height:100%;background:var(--slate);border:2px solid #ddd;padding:8px 8px}
.hours h2{font-weight:400;font-size:21px;color:var(--white);text-align:center}
.hours .open{font-size:17px;color:var(--hours-text);margin-top:12px}
.hours h3{font-size:13px;color:var(--white);margin-top:16px}
.hours p{font-size:12.5px;color:var(--hours-text);line-height:18px}

/* dish cards */
.card{top:720px;width:256px;height:210px}
.card .frame{left:0;top:10px;width:256px;height:200px;background:var(--red)}
.card .photo{left:11px;top:65px;width:234px;height:134px}
.card .banner{left:11px;top:0;width:234px;height:66px}
.card .title{left:11px;top:4px;width:234px;text-align:center;font-family:"Almendra",serif;font-style:italic;font-weight:700;font-size:18px;line-height:17px;color:var(--white)}

/* specials */
.specials{left:0;top:963px;width:922px;height:147px;background:var(--red)}
.section-title{top:966px;font-size:21px;line-height:24px;color:var(--white);text-align:center}
.list{font-weight:700;font-size:12px;color:var(--white);line-height:20px;letter-spacing:.2px}

/* footer */
.footer{left:0;top:1110px;width:922px;height:90px;background:var(--footer)}
.footer-nav a{position:absolute;top:1130px;font-size:13px;color:var(--white);text-decoration:none}
.footer-nav a.active{color:var(--red)}
.copyright{left:0;top:1160px;width:922px;text-align:center;font-size:11px;color:var(--white)}
.copyright b{color:var(--red);font-weight:400}
</style>
</head>
<body>

<div class="abs topbar"></div>
<div class="abs reservation">
  <svg width="16" height="16" viewBox="0 0 24 24"><path fill="#fff" d="M6.6 10.8a15 15 0 0 0 6.6 6.6l2.2-2.2c.3-.3.7-.4 1-.2 1.1.4 2.3.6 3.6.6.6 0 1 .4 1 1V20c0 .6-.4 1-1 1A17 17 0 0 1 3 4c0-.6.4-1 1-1h3.5c.6 0 1 .4 1 1 0 1.3.2 2.5.6 3.6.1.3 0 .7-.2 1z"/></svg>
  Make a Reservation : +44 100 200 3000
</div>
<div class="abs social">
  <span aria-label="Social link 1"></span>
  <span aria-label="Social link 2"></span>
  <span aria-label="Social link 3"></span>
  <span aria-label="Social link 4"></span>
  <span aria-label="Email">
    <svg width="16" height="12" viewBox="0 0 16 12"><rect x="0" y="0" width="16" height="12" rx="1.5" fill="#e8252a"/><path d="M1 1.5 8 7l7-5.5" stroke="#fff" stroke-width="1.6" fill="none"/></svg>
  </span>
</div>

<div class="abs header"></div>
<div class="abs ornament left" role="img" aria-label="Orange floral swirl ornament"></div>
<div class="abs ornament right" role="img" aria-label="Orange floral swirl ornament"></div>
<div class="abs logo-arch">
  <span class="mark"></span>
  <span class="name">CHEF WEN<br>CHINESE RESTAURANT</span>
</div>

<nav class="abs nav">
  <a class="active" style="left:162px">Home</a>
  <a style="left:243px">About</a>
  <a style="left:328px">Menu</a>
  <a style="left:406px">Winelist</a>
  <a style="left:505px">Facilities</a>
  <a style="left:610px">Gallery</a>
  <a style="left:700px">Contact</a>
</nav>

<div class="abs hero" role="img" aria-label="Dining table set with wine glasses and appetisers, with wine being poured"></div>
<div class="abs dots"><span class="on"></span><span></span><span></span><span></span></div>

<h1 class="abs welcome-title" style="font-weight:400">Welcome to&nbsp; Chef Wen</h1>
<svg class="abs divider" viewBox="0 0 486 36">
  <g stroke="#e8252a" stroke-width="1"><line x1="0" y1="16" x2="218" y2="16"/><line x1="0" y1="19" x2="218" y2="19"/><line x1="268" y1="16" x2="486" y2="16"/><line x1="268" y1="19" x2="486" y2="19"/></g>
  <circle cx="243" cy="18" r="18" fill="#e8252a"/>
  <path d="M233 19 243 10l10 9h-3v8h-5v-5h-4v5h-5v-8z" fill="#fff"/>
</svg>
<div class="abs welcome-text">
  <p>Chef Wen is named after its’ executive chef, Mr. Wen. Chef Wen has been in his career for nearly two decades before he moved to Australia nine years ago. He settled in Adelaide then started his first restaurant, Lantern Court in Norwood. Lantern Court has been running successfully for years due to Chef Wen’s talent of cooking.</p>
  <p>We offer an exceptional dining experience with authentic and dynamic dishes created with quality ingredients. The menu of Chef Wen is based on classic Cantonese dishes, featured by southern China’s local flavour characteristics. Taking advantage of South Australia’s rich and quality food resources...</p>
</div>
<div class="abs read-more">READ MORE</div>

<div class="abs hours">
  <div class="hours-inner">
    <h2>Opening Hours</h2>
    <div class="open">We are open 7 days</div>
    <h3>Lunch :</h3>
    <p>Monday to Friday 11:30am – 2:30pm<br>Saturday to Sunday 11:00am – 3:00pm</p>
    <h3>Dinner :</h3>
    <p>Monday to Sunday 6:00pm Until Late</p>
  </div>
</div>

<!-- dish cards -->
<div class="abs card" style="left:59px">
  <div class="abs frame"></div>
  <div class="abs photo" role="img" aria-label="Steamed pork ribs with chilli in a bowl" style="background:linear-gradient(160deg,#f2ece4,#b8764a,#8a4a2a)"></div>
  <svg class="abs banner" viewBox="0 0 234 66"><polygon points="0,0 234,0 234,66 117,50 0,66" fill="#2e2e2e"/><line x1="5" y1="0" x2="5" y2="62" stroke="#555" stroke-width="3"/><line x1="229" y1="0" x2="229" y2="62" stroke="#555" stroke-width="3"/></svg>
  <div class="abs title" style="top:7px">Steamed Pork Ribs</div>
</div>
<div class="abs card" style="left:331px">
  <div class="abs frame"></div>
  <div class="abs photo" role="img" aria-label="Slices of brown Malay sponge cake" style="background:linear-gradient(160deg,#f4f4f0,#c0683a,#9a4a24)"></div>
  <svg class="abs banner" viewBox="0 0 234 66"><polygon points="0,0 234,0 234,66 117,50 0,66" fill="#2e2e2e"/><line x1="5" y1="0" x2="5" y2="62" stroke="#555" stroke-width="3"/><line x1="229" y1="0" x2="229" y2="62" stroke="#555" stroke-width="3"/><line x1="80" y1="31" x2="154" y2="31" stroke="#fff" stroke-width="1"/></svg>
  <div class="abs title" style="top:7px">Malay Cakes</div>
</div>
<div class="abs card" style="left:603px">
  <div class="abs frame"></div>
  <div class="abs photo" role="img" aria-label="Pan-fried white radish cakes on a plate" style="background:linear-gradient(160deg,#f6f2ea,#e6b070,#f4eee4)"></div>
  <svg class="abs banner" viewBox="0 0 234 66"><polygon points="0,0 234,0 234,66 117,50 0,66" fill="#2e2e2e"/><line x1="5" y1="0" x2="5" y2="62" stroke="#555" stroke-width="3"/><line x1="229" y1="0" x2="229" y2="62" stroke="#555" stroke-width="3"/><line x1="80" y1="47" x2="154" y2="47" stroke="#fff" stroke-width="1"/></svg>
  <div class="abs title" style="top:5px">Fried White Radish<br>Patey</div>
</div>

<!-- specials and location -->
<div class="abs specials"></div>
<h2 class="abs section-title" style="left:223px;width:200px;font-weight:400">Special Dishes</h2>
<h2 class="abs section-title" style="left:634px;width:200px;font-weight:400">Location</h2>
<svg class="abs" style="left:79px;top:990px" width="486" height="36" viewBox="0 0 486 36">
  <g stroke="#fff" stroke-width="1"><line x1="0" y1="16" x2="220" y2="16"/><line x1="0" y1="19" x2="220" y2="19"/><line x1="268" y1="16" x2="486" y2="16"/><line x1="268" y1="19" x2="486" y2="19"/></g>
  <circle cx="244" cy="18" r="18" fill="#fff"/>
  <g fill="#e8252a"><rect x="236" y="9" width="2" height="8"/><rect x="240" y="9" width="2" height="8"/><rect x="236" y="15" width="6" height="3"/><rect x="238" y="16" width="2.5" height="12"/><path d="M247 9c3 0 3.5 5 3.5 9h-1.5v10h-2.5z"/></g>
</svg>
<svg class="abs" style="left:601px;top:990px" width="262" height="36" viewBox="0 0 262 36">
  <g stroke="#fff" stroke-width="1"><line x1="0" y1="16" x2="107" y2="16"/><line x1="0" y1="19" x2="107" y2="19"/><line x1="155" y1="16" x2="262" y2="16"/><line x1="155" y1="19" x2="262" y2="19"/></g>
  <circle cx="131" cy="18" r="18" fill="#fff"/>
  <path d="M131 28c-4-5-6-8-6-11a6 6 0 0 1 12 0c0 3-2 6-6 11z" fill="#e8252a"/><circle cx="131" cy="17" r="2.3" fill="#fff"/>
</svg>
<div class="abs list" style="left:63px;top:1018px">Prawn Dumplings<br>Scallop Dumplings<br>Vegetarian Dumplings<br>Minced Pork &amp; Peanut Dumplings</div>
<div class="abs list" style="left:335px;top:1018px">Steamed Custard Bun with Egg Yolk<br>Spicy Chicken Feet in Black bean Sauce<br>Steamed Pork Ribs<br>Spicy Ox Tripe</div>
<div class="abs list" style="left:606px;top:1026px">Restaurant Name<br>Area name,<br>City, State, Country</div>

<footer class="abs footer"></footer>
<div class="footer-nav">
  <a class="active" style="left:168px">Home</a>
  <a style="left:243px">About</a>
  <a style="left:328px">Menu</a>
  <a style="left:406px">Winelist</a>
  <a style="left:506px">Facilities</a>
  <a style="left:611px">Events</a>
  <a style="left:700px">Contact</a>
</div>
<div class="abs copyright">© <b>Chef Wen</b> - 2014. All Rights Reserved.</div>

</body>
</html>
```